RW Framewell Inc Business cards

We need business cards using our existing logo but slightly modified. Right now the logo says RW Loadbearing Masonry. We want to keep the RW part of the design, but replace the Structural Concrete portion with "FRAMEWELL". Please see the attached file.
Ideally this would be a blank template so we can add Different Names, titles, and phone numbers later.
On the one side we want only the logo and on the other side the detail. I'm attaching an example for you to see.
Please reach out with any other questions. Our address and other details will be given out once we find a design we like.

Target Market(s)

Construction Industry

```html
<!DOCTYPE html>
<html lang="en">
<head>
<meta charset="UTF-8">
<title>RW Framewell Inc Business Cards</title>
<link rel="stylesheet" href="https://fonts.googleapis.com/css2?family=Montserrat:wght@600;700&family=Roboto:wght@400&display=swap">
<style>
  :root {
    --backdrop: #3b3b3d;
    --card-black: #1d1d1f;
    --card-black-soft: #242426;
    --stripe-grey: #6e6e70;
    --brand-blue: #2f64a8;
    --name-blue: #3a78c9;
    --logo-grey: #5c5c60;
    --white: #ffffff;
  }
  * { box-sizing: border-box; margin: 0; padding: 0; }
  html, body {
    width: 799px;
    height: 1200px;
    overflow: hidden;
    background: var(--backdrop);
  }
  .sheet {
    position: relative;
    width: 799px;
    height: 1200px;
  }
  .card {
    position: absolute;
    left: 90px;
    width: 620px;
    height: 354px;
    border-radius: 4px;
    overflow: hidden;
    box-shadow: 0 10px 24px rgba(0, 0, 0, 0.45);
  }
  .card--front {
    top: 110px;
    background: var(--card-black);
    display: flex;
    align-items: center;
    justify-content: center;
  }
  .front-wordmark {
    font-family: "Montserrat", sans-serif;
    font-weight: 700;
    font-size: 50px;
    letter-spacing: 6px;
    color: var(--logo-grey);
  }
  .card--back {
    top: 720px;
    background: var(--brand-blue);
  }
  .back-header {
    position: absolute;
    top: 0; left: 0; right: 0;
    height: 112px;
    background: var(--card-black-soft);
    padding: 30px 0 0 34px;
  }
  .back-stripe {
    position: absolute;
    top: 112px; left: 0; right: 0;
    height: 10px;
    background: var(--stripe-grey);
  }
  .person-name {
    font-family: "Montserrat", sans-serif;
    font-weight: 600;
    font-size: 20px;
    color: var(--name-blue);
  }
  .person-title {
    font-family: "Roboto", sans-serif;
    font-size: 13px;
    color: var(--white);
    margin-top: 4px;
  }
  .contact-list {
    position: absolute;
    top: 150px;
    left: 34px;
    list-style: none;
    font-family: "Roboto", sans-serif;
    font-size: 14px;
    line-height: 1.4;
    color: var(--white);
  }
  .contact-list li {
    display: flex;
    align-items: center;
    gap: 10px;
  }
  .contact-list .address { padding-left: 24px; margin-bottom: 4px; }
  .contact-list svg { width: 14px; height: 14px; flex: none; }
  .back-wordmark {
    position: absolute;
    right: 34px;
    bottom: 50px;
    font-family: "Montserrat", sans-serif;
    font-weight: 700;
    font-size: 30px;
    letter-spacing: 4px;
    color: var(--white);
  }
</style>
</head>
<body>
<main class="sheet">
  <section class="card card--front" aria-label="Business card front">
    <p class="front-wordmark">RW FRAMEWELL</p>
  </section>

  <section class="card card--back" aria-label="Business card back">
    <header class="back-header">
      <h1 class="person-name">Alex RW Morgan</h1>
      <p class="person-title">Managing Director</p>
    </header>
    <div class="back-stripe"></div>

    <ul class="contact-list">
      <li class="address">118 Sample Rd., Any Town,<br>Nevada, US 654321</li>
      <li>
        <svg viewBox="0 0 16 16" aria-hidden="true"><path fill="#fff" d="M3.5 1.5l2.5 0 1 3.5-1.7 1.2a9 9 0 0 0 4.5 4.5L11 9l3.5 1v2.5c0 1-1 2-2 2A11 11 0 0 1 1.5 3.5c0-1 1-2 2-2z"/></svg>
        555-010-2020
      </li>
      <li>
        <svg viewBox="0 0 16 16" aria-hidden="true"><rect x="1.5" y="3.5" width="13" height="9" fill="none" stroke="#fff" stroke-width="1.4"/><path d="M1.5 3.5L8 9l6.5-5.5" fill="none" stroke="#fff" stroke-width="1.4"/></svg>
        alex@framewell-example.com
      </li>
      <li>
        <svg viewBox="0 0 16 16" aria-hidden="true"><circle cx="8" cy="8" r="6.3" fill="none" stroke="#fff" stroke-width="1.3"/><ellipse cx="8" cy="8" rx="2.6" ry="6.3" fill="none" stroke="#fff" stroke-width="1.1"/><path d="M1.7 8h12.6" stroke="#fff" stroke-width="1.1"/></svg>
        www.framewell-example.com
      </li>
    </ul>

    <p class="back-wordmark">RW FRAMEWELL</p>
  </section>
</main>
</body>
</html>
```